Looking for a modern, Professional business card design

We have a simple business card, but are looking for a more modern, professional look. A sample of the basic card is attached as well as the logo. We would also like to add that we offer:
Struggling with your finances?
- Learn to become debt free
- Discover the power of cash
- Control your money instead of it controlling you
Let us help you achieve a new level of financial freedom!
Also, we would like to have a "SPECIAL OFFER!: FREE 30 minute consultation"
Financial Planning

```html
<!DOCTYPE html>
<html lang="en">
<head>
<meta charset="UTF-8">
<title>Harbor Money Coaching – Business Card</title>
<link href="https://fonts.googleapis.com/css2?family=Open+Sans:wght@400;600;700&display=swap" rel="stylesheet">
<style>
  :root{
    --page:#e9e6e2;
    --card:#0d0d0d;
    --ink:#f2f2f2;
    --muted:#cfcfcf;
    --green:#7dc242;
    --green-dark:#4f9a2a;
    --rule:#2e2e2e;
  }
  *{box-sizing:border-box;margin:0;padding:0}
  html,body{width:1200px;height:900px;overflow:hidden}
  body{
    background:var(--page);
    font-family:"Open Sans",Arial,sans-serif;
    position:relative;
  }
  .card{
    position:absolute;
    width:525px;height:300px;
    background:var(--card);
    border-radius:3px;
    box-shadow:0 10px 24px rgba(0,0,0,.28);
    color:var(--ink);
  }
  .card--front{left:50px;top:300px}
  .card--back{left:625px;top:300px}

  /* front */
  .brand-mark{
    position:absolute;left:34px;top:118px;
    display:flex;align-items:center;gap:10px;
    color:var(--green);font-weight:700;font-size:17px;line-height:1.2;
  }
  .brand-mark__dot{width:16px;height:16px;border-radius:50%;background:var(--green);flex:none}
  .front-divider{position:absolute;left:238px;top:60px;width:1px;height:180px;background:var(--rule)}
  .contact{position:absolute;left:262px;top:78px}
  .contact__name{color:var(--green);font-weight:700;font-size:19px;line-height:1.2}
  .contact__role{font-size:15px;color:var(--ink);margin-bottom:22px}
  .contact__list{list-style:none}
  .contact__item{display:flex;align-items:center;gap:10px;font-size:14.5px;line-height:1.55}
  .contact__icon{width:11px;height:11px;flex:none;fill:var(--green)}

  /* back */
  .back-brand{
    position:absolute;left:0;right:0;top:34px;
    display:flex;justify-content:center;align-items:center;gap:10px;
    font-weight:700;font-size:24px;color:var(--muted);letter-spacing:.5px;
  }
  .back-brand__dot{width:18px;height:18px;border-radius:50%;background:var(--muted)}
  .pitch{position:absolute;left:48px;top:104px;right:30px}
  .pitch__question{font-weight:700;font-size:15.5px;margin-bottom:6px}
  .pitch__list{list-style:none;margin-left:34px}
  .pitch__list li{font-size:14px;line-height:1.45;display:flex;align-items:center;gap:8px}
  .pitch__list li::before{content:"";border-left:7px solid var(--ink);border-top:4px solid transparent;border-bottom:4px solid transparent}
  .pitch__list li.pitch__wide{margin-left:-34px}
  .pitch__closing{font-size:14px;margin-top:12px}
  .pitch__offer{font-weight:600;font-size:17.5px;margin-top:10px;letter-spacing:.2px}
</style>
</head>
<body>
  <section class="card card--front" aria-label="Business card front">
    <div class="brand-mark"><span class="brand-mark__dot"></span>Harbor Money<br>Coaching</div>
    <div class="front-divider"></div>
    <div class="contact">
      <p class="contact__name">Daniel R. Hayes</p>
      <p class="contact__role">Personal financial coach</p>
      <ul class="contact__list">
        <li class="contact__item">
          <svg class="contact__icon" viewBox="0 0 12 12"><path d="M2.5 0.5l2 2.5-1.2 1.2a7 7 0 0 0 4.5 4.5L9 7.5l2.5 2-1.5 2C5 11.5 0.5 7 0.5 2z"/></svg>
          (555) 014-2290
        </li>
        <li class="contact__item">
          <svg class="contact__icon" viewBox="0 0 12 12"><path d="M0 2h12v8H0z M0.8 2.6L6 6.6l5.2-4" stroke="#0d0d0d" stroke-width="1"/></svg>
          daniel@steadymoneypath.com
        </li>
        <li class="contact__item">
          <svg class="contact__icon" viewBox="0 0 12 12"><circle cx="6" cy="6" r="5.5"/><path d="M0.5 6h11M6 0.5c-3 3-3 8 0 11M6 0.5c3 3 3 8 0 11" stroke="#0d0d0d" stroke-width=".8" fill="none"/></svg>
          www.steadymoneypath.com
        </li>
      </ul>
    </div>
  </section>

  <section class="card card--back" aria-label="Business card back">
    <div class="back-brand"><span class="back-brand__dot"></span>HARBOR MONEY COACHING</div>
    <div class="pitch">
      <p class="pitch__question">Struggling with your finances?</p>
      <ul class="pitch__list">
        <li>Learn to become debt free</li>
        <li>Discover the power of cash</li>
        <li class="pitch__wide">Control your money instead of it controlling you</li>
      </ul>
      <p class="pitch__closing">Let us help you achieve a new level of financial freedom!</p>
      <p class="pitch__offer">SPECIAL OFFER!: FREE 30 MINUTE CONSULTATION</p>
    </div>
  </section>
</body>
</html>
```